Logo for a Food & Beverage Franchise Company

We need a logo and stationary for a new company that just aquired a restaurant franchise. We need a sleep and professional logo with stationary.

Target Market(s)

Adults, resturaunt owners, franchisors (Companies who own food franchise companies such as Farrowbys Head Office, Toastwell International Franchise)
and Big Food and Beverage who wish to give franchise rights to us)

Industry/Entity Type

Restaurant

Logo Text

Velvet Harbor

Logo styles of interest
Emblem Logo
Pictorial/Combination Logo
Character Logo
Font styles to use
Serif
Sans Serif

Colors
ffc214
f78f20
f37022
faa54b
fece3e
fbed22

Requirements
Must have
• Maximum three color. The less the better.
Nice to have
• It does not have to have a crown, but if you wish to have a crown then it does not have to be so sharp and clear. Abstract is better.

```html
<!DOCTYPE html>
<html lang="en">
<head>
<meta charset="utf-8">
<title>Velvet Harbor — Business Card</title>
<link rel="stylesheet" href="https://fonts.googleapis.com/css2?family=Crimson+Text:wght@400;600&display=swap">
<style>
  :root {
    --backdrop: #e4ece7;
    --card: #15181b;
    --gold: #f5b316;
    --orange: #f37022;
    --ink-light: #f4f1ea;
    --swirl: rgba(255,255,255,0.05);
  }
  * { margin: 0; padding: 0; box-sizing: border-box; }
  html, body {
    width: 1200px; height: 1200px; overflow: hidden;
    background: var(--backdrop);
    font-family: "Crimson Text", Georgia, serif;
  }
  .canvas {
    position: relative; width: 1200px; height: 1200px;
  }
  .card {
    position: absolute; left: 180px; width: 840px; height: 480px;
    background: var(--card);
    box-shadow: 0 10px 28px rgba(0,0,0,0.18);
    overflow: hidden;
  }
  .card--front { top: 90px; }
  .card--back { top: 630px; }

  /* front */
  .corner-flourish {
    position: absolute; width: 150px; height: 220px; top: 130px;
    background: radial-gradient(ellipse at center, var(--swirl), transparent 70%);
  }
  .corner-flourish--left { left: -40px; }
  .corner-flourish--right { right: -40px; }
  .brand {
    position: absolute; display: flex; align-items: center; gap: 16px;
  }
  .brand__mark {
    width: 22px; height: 22px; background: var(--orange);
  }
  .brand__name {
    color: var(--gold); font-weight: 600; letter-spacing: 0.5px;
    white-space: nowrap;
  }
  .card--front .brand {
    left: 50%; top: 50%; transform: translate(-50%, -50%);
  }
  .card--front .brand__name { font-size: 54px; }

  /* back */
  .card--back .brand {
    left: 70px; top: 70px;
  }
  .card--back .brand__name { font-size: 42px; }
  .brand-rule {
    position: absolute; left: 70px; top: 135px; width: 300px;
  }
  .brand-rule span {
    display: block; height: 3px; background: var(--gold); margin-bottom: 6px;
  }
  .address {
    position: absolute; left: 48px; top: 262px;
    color: var(--ink-light); font-size: 21px;
  }
  .person {
    position: absolute; right: 60px; top: 280px; text-align: right;
  }
  .person__name {
    color: var(--gold); font-size: 30px; font-weight: 600; letter-spacing: 1px; line-height: 1;
  }
  .person__title {
    color: var(--ink-light); font-size: 17px; letter-spacing: 2.5px; margin-top: 2px;
  }
  .person__rule {
    height: 3px; background: var(--gold); width: 210px; margin: 6px 0 0 auto;
  }
  .contacts {
    position: absolute; right: 60px; top: 362px; list-style: none;
  }
  .contacts li {
    display: flex; align-items: center; justify-content: flex-end; gap: 14px;
    color: var(--ink-light); font-size: 21px; line-height: 30px;
  }
  .contacts svg { width: 20px; height: 20px; flex: none; }
</style>
</head>
<body>
<main class="canvas">

  <section class="card card--front" aria-label="Business card front">
    <div class="corner-flourish corner-flourish--left" role="img" aria-label="Faint decorative flourish"></div>
    <div class="corner-flourish corner-flourish--right" role="img" aria-label="Faint decorative flourish"></div>
    <div class="brand">
      <span class="brand__mark"></span>
      <span class="brand__name">Velvet Harbor</span>
    </div>
  </section>

  <section class="card card--back" aria-label="Business card back">
    <div class="brand">
      <span class="brand__mark"></span>
      <span class="brand__name">Velvet Harbor</span>
    </div>
    <div class="brand-rule"><span></span><span></span></div>

    <p class="address">48 Pier Lane Westport, VH 210</p>

    <div class="person">
      <p class="person__name">Idris Calder</p>
      <p class="person__title">Managing Director</p>
      <div class="person__rule"></div>
    </div>

    <ul class="contacts">
      <li>(041) 552870-14
        <svg viewBox="0 0 20 20" aria-hidden="true"><rect width="20" height="20" rx="3" fill="var(--gold)"/><path d="M6 4c1 0 2 2 2 3s-1 1-1 2 2 3 3 3 1-1 2-1 3 1 3 2-1 3-3 3C8 16 4 11 4 7c0-2 1-3 2-3z" fill="var(--card)"/></svg>
      </li>
      <li>hello@velvetharbor.co
        <svg viewBox="0 0 20 20" aria-hidden="true"><rect x="2" y="5" width="16" height="11" fill="none" stroke="var(--gold)" stroke-width="1.5"/><path d="M2 5l8 6 8-6" fill="none" stroke="var(--gold)" stroke-width="1.5"/></svg>
      </li>
      <li>www.velvetharbor.co
        <svg viewBox="0 0 20 20" aria-hidden="true"><circle cx="10" cy="10" r="8" fill="none" stroke="var(--gold)" stroke-width="1.5"/><ellipse cx="10" cy="10" rx="3.5" ry="8" fill="none" stroke="var(--gold)" stroke-width="1.2"/><path d="M2 10h16M4 6h12M4 14h12" stroke="var(--gold)" stroke-width="1.2"/></svg>
      </li>
    </ul>
  </section>

</main>
</body>
</html>
```